I have a website called Okenta Holdings (okentaholdings.com) that I would like to have redesigned. Most of the content is already created, but I need a new design. You can also see my other website at brambleacres.com. I am open to a new logo or modifying the current logo if you have a good idea. Please feel free to use other images for the home page (and maybe some other locations) if you feel they provide a better look and feel to the website. I prefer a modern look.

Important: You do not have to use the images I've provided for the home page. Feel free to find your own stock photos. You don't have to pay for them unless I select your design.

1) Please use wix.com to make your changes so that I can edit it later.
2) I will need all the graphics files to be saved so I can dowload it for later.
3) I will be adding more content to the site later.
4) This site will likely be transferred over to brambleacres.com so if you make a logo please make one for Okenta Holdings and one for Bramble Acres.
5) You can use other images that you feel would help the look and feel of the website.

```html
<!DOCTYPE html>
<html lang="en">
<head>
<meta charset="utf-8">
<title>Bramble Acres</title>
<link rel="stylesheet" href="https://fonts.googleapis.com/css2?family=Inter+Tight:wght@400;500;600&display=swap">
<style>
:root{
  --blue:#3a8be0;
  --blue-deep:#1f6fc6;
  --blue-light:#4fa6f2;
  --ink:#1b1f27;
  --text:#555b66;
  --muted:#8a909a;
  --line:#d9dde3;
  --footer:#0c1a33;
  --white:#fff;
  --star:#f5a000;
}
*{box-sizing:border-box;margin:0;padding:0}
html,body{width:1200px;height:3771px;overflow:hidden}
body{font-family:"Inter Tight",Arial,sans-serif;color:var(--ink);background:var(--white);position:relative}
.abs{position:absolute}
.btn{position:absolute;display:flex;align-items:center;justify-content:center;background:var(--blue);color:#fff;border-radius:8px;font-size:18px;font-weight:500}
.brand{position:absolute;display:flex;align-items:center;gap:12px;font-weight:600;font-size:27px;line-height:1;letter-spacing:-.5px}
.brand i{width:36px;height:36px;border-radius:50%;background:var(--blue);display:block}
/* nav */
.nav-link{position:absolute;top:38px;font-size:18px;letter-spacing:-.3px}
/* hero */
.hero{left:0;top:100px;width:1200px;height:652px;background:radial-gradient(ellipse at 50% 40%,#5b4a5e 0%,#3a3a4c 45%,#22252f 100%)}
.hero-title{left:0;width:1200px;text-align:center;font-size:80px;font-weight:500;letter-spacing:-4px;line-height:72px;color:#fff}
.hero-sub{left:0;top:448px;width:1200px;text-align:center;font-size:28px;line-height:31px;color:#fff;letter-spacing:-.8px}
.partners{left:0;top:752px;width:1200px;height:98px;background:#3f4557}
.badge{position:absolute;top:786px;height:30px;border-radius:6px;background:#c9ccd3}
/* about */
.photo{position:absolute}
.h-sec{font-size:38px;font-weight:500;letter-spacing:-1.2px;line-height:36px}
.para{font-size:19px;line-height:25px;color:var(--text);letter-spacing:-.3px}
.caption{position:absolute;top:1907px;font-size:19px;color:var(--text)}
/* strategy */
.card{position:absolute;background:#fff;border-radius:14px;box-shadow:0 10px 40px rgba(30,60,110,.15);padding:26px 28px}
.card h3{color:var(--blue-deep);font-size:27px;font-weight:500;text-align:center;letter-spacing:-.8px;line-height:28px}
.card p,.card li{font-size:19px;color:var(--text);line-height:35px;letter-spacing:-.3px}
.card ul{list-style:none}
.card li{padding-left:18px;position:relative}
.card li:before{content:"";position:absolute;left:2px;top:16px;width:4px;height:4px;border-radius:50%;background:var(--muted)}
/* testimonials */
.tcard{position:absolute;top:3104px;width:330px;height:253px;background:#fff;border-radius:14px;box-shadow:0 8px 30px rgba(30,60,110,.1);padding:20px 20px}
.avatar{width:68px;height:68px;border-radius:8px;background:linear-gradient(#f2b24a,#e28a2b)}
.stars{position:absolute;right:18px;top:38px;display:flex;gap:6px}
.tname{margin-top:14px;font-size:19px;font-weight:600}
.tbody{margin-top:10px;font-size:17.5px;line-height:24px;color:var(--text)}
.arrow{position:absolute;top:3199px;width:40px;height:40px;border-radius:50%;background:#fff;box-shadow:0 4px 14px rgba(0,0,0,.12);display:flex;align-items:center;justify-content:center}
/* footer */
.footer{left:0;top:3437px;width:1200px;height:334px;background:var(--footer)}
.f-head{position:absolute;top:3498px;font-size:18px;font-weight:600;color:var(--blue-light)}
.f-link{position:absolute;font-size:18px;color:#fff}
.social{position:absolute;top:3732px;width:20px;height:20px;border:1.6px solid #8a93a6;border-radius:50%}
</style>
</head>
<body>

<!-- header -->
<div class="brand" style="left:83px;top:30px;color:var(--blue-deep)"><i></i>Bramble Acres</div>
<div class="nav-link" style="left:439px">Home</div>
<div class="nav-link" style="left:521px">About</div>
<div class="nav-link" style="left:601px">Strategy</div>
<div class="nav-link" style="left:698px">Projects</div>
<div class="btn" style="left:964px;top:19px;width:152px;height:62px">Contact us</div>

<!-- hero -->
<div class="abs hero" role="img" aria-label="Aerial view of a construction site with cranes at dusk"></div>
<div class="abs hero-title" style="top:278px">Building Together</div>
<div class="abs hero-title" style="top:350px;color:var(--blue-light)">Growing Together</div>
<div class="abs hero-sub">Private Commercial Real Estate<br>Investment And Development Firm</div>
<div class="btn" style="left:512px;top:543px;width:176px;height:63px">Get Started</div>

<div class="abs partners"></div>
<div class="abs" style="left:142px;top:788px;font-size:22px;color:#fff;letter-spacing:-.4px">Corporate Partners</div>
<div class="abs" style="left:375px;top:780px;width:3px;height:42px;background:#fff"></div>
<div class="badge" style="left:418px;width:98px"></div>
<div class="badge" style="left:565px;width:98px"></div>
<div class="badge" style="left:713px;width:98px"></div>
<div class="badge" style="left:855px;width:110px"></div>
<div class="badge" style="left:1008px;width:100px"></div>

<!-- about -->
<div class="photo" style="left:83px;top:938px;width:454px;height:442px;background:linear-gradient(135deg,#1c2a4a,#3d4b6a 40%,#6b6a4a 70%,#2a2e24)" role="img" aria-label="Modern residential courtyard with glass lounge, reflecting pool and lit green wall at dusk"></div>
<div class="abs h-sec" style="left:587px;top:940px">About</div>
<div class="abs h-sec" style="left:587px;top:976px;color:var(--blue-deep)">Bramble Acres</div>
<p class="abs para" style="left:587px;top:1039px;width:530px">Bramble Acres is a private real estate firm that specializes in the procurement, development, management, and disposition of various commercial real estate asset types including multifamily, industrial, single-family, hospitality, self-storage, and flex. The firm effectuates its strategy by utilizing long-standing relationships to ascertain acquisition and development opportunities within a specific target market. Bramble Acres is currently focused on acquisition and development opportunities in the southern portion of the United States.</p>
<div class="btn" style="left:587px;top:1317px;width:184px;height:63px">Learn More</div>

<div class="abs" style="left:83px;top:1452px;width:1032px;height:2px;background:var(--line)"></div>

<!-- projects -->
<div class="abs h-sec" style="left:0;width:1200px;text-align:center;top:1500px;color:#333">Top Projects</div>
<div class="photo" style="left:83px;top:1563px;width:327px;height:327px;background:linear-gradient(160deg,#d9cdb8,#b69c80 45%,#5f7a52 80%,#8a8f8a)" role="img" aria-label="Rendering of a residential building with arched ground floor and landscaped street"></div>
<div class="photo" style="left:436px;top:1563px;width:326px;height:327px;background:linear-gradient(180deg,#eef2f6,#6b5a55 45%,#7fa55a 75%,#c9cec9)" role="img" aria-label="Rendering of apartment buildings around a landscaped lawn"></div>
<div class="photo" style="left:789px;top:1563px;width:326px;height:327px;background:linear-gradient(180deg,#2e6fd0 0%,#e8e8ea 35%,#cfd0d2 85%,#a9a69a)" role="img" aria-label="White industrial warehouse building under a blue sky"></div>
<div class="caption" style="left:83px">Stonebrook Harbor Residences</div>
<div class="caption" style="left:436px">Lakeview at Cedar Run</div>
<div class="caption" style="left:789px">Ridgeline Industrial</div>

<!-- strategies -->
<div class="abs" style="left:0;top:2077px;width:1200px;height:753px;background:linear-gradient(100deg,#3b4150 0%,#5a5d66 45%,#4a4a4e 75%,#2d3038)" role="img" aria-label="Modern multifamily apartment building at street level"></div>
<div class="abs" style="left:85px;top:2288px;font-size:66px;font-weight:600;letter-spacing:-3px;line-height:57px;color:#fff">Motives and<br>strategies of<br><span style="color:var(--blue-light)">Bramble<br>Acres</span></div>
<div class="btn" style="left:85px;top:2556px;width:183px;height:61px">Our Strategies</div>

<div class="card" style="left:803px;top:2044px;width:324px;height:396px">
  <h3>Development</h3>
  <p style="margin-top:24px;line-height:24px">Site Selection:</p>
  <ul><li>Undeveloped Land</li><li>Entitled Land</li><li>Urban Redevelopment</li></ul>
  <p style="line-height:24px">Multiple Construction Types:</p>
  <ul><li>Single Story Garden</li><li>Wrap Construction</li><li>Podium Construction</li><li>Tiltwall</li></ul>
</div>
<div class="card" style="left:543px;top:2326px;width:244px;height:326px">
  <h3>Product Types</h3>
  <ul style="margin-top:20px"><li>Multifamily</li><li>Industrial</li><li>SFR Communities</li><li>Self-Storage</li><li>Hospitality</li><li>Retail</li></ul>
</div>
<div class="card" style="left:803px;top:2461px;width:324px;height:326px">
  <h3>Acquisitions:<br>Distressed/Value-Add</h3>
  <ul style="margin-top:24px"><li style="line-height:24px;margin-bottom:10px">Assets which yeild cash-on-cash returns as well as rent growth and exit upside.</li><li>Major Metropolitan Areas</li><li style="line-height:24px;margin-top:6px">Asset Value between $10 - $75mm</li></ul>
</div>
<div class="card" style="left:497px;top:2688px;width:290px;height:241px">
  <h3>Investment Focus</h3>
  <ul style="margin-top:16px"><li>Ground-up Development</li><li>Value-Add Acquisition</li><li>Equity Financing</li><li>Debt Financing</li></ul>
</div>

<!-- testimonials -->
<div class="abs" style="left:0;width:1200px;top:3006px;text-align:center;font-size:40px;font-weight:500;letter-spacing:-1.5px;line-height:32px;color:var(--blue-deep)">Our work and quality<br>speak for themselves</div>

<div class="arrow" style="left:28px"><svg width="18" height="18" viewBox="0 0 18 18"><path d="M15 9H3M8 4 3 9l5 5" fill="none" stroke="#3a8be0" stroke-width="2"/></svg></div>
<div class="arrow" style="left:1132px"><svg width="18" height="18" viewBox="0 0 18 18"><path d="M3 9h12M10 4l5 5-5 5" fill="none" stroke="#3a8be0" stroke-width="2"/></svg></div>

<div class="tcard" style="left:83px">
  <div class="avatar" role="img" aria-label="Client portrait"></div>
  <div class="stars"><svg width="168" height="26" viewBox="0 0 168 26"><g fill="#f5a000" stroke="#f5a000" stroke-width="1.5"><path id="s" d="M13 2l3.2 7 7.6.8-5.7 5.1 1.6 7.5L13 18.6 6.3 22.4l1.6-7.5L2.2 9.8l7.6-.8z"/><use href="#s" x="35"/><use href="#s" x="70"/><use href="#s" x="105" fill="none"/><use href="#s" x="140" fill="none"/></g></svg></div>
  <div class="tname">Nora Bell</div>
  <div class="tbody">Amet minim mollit non deserunt ullamco est sit aliqua dolor do amet sint. Velit officia consequat duis enim velit mollit....</div>
</div>
<div class="tcard" style="left:436px">
  <div class="avatar" style="background:linear-gradient(#8fd3e8,#4ba8c9)" role="img" aria-label="Client portrait"></div>
  <div class="stars"><svg width="168" height="26" viewBox="0 0 168 26"><g fill="#f5a000" stroke="#f5a000" stroke-width="1.5"><use href="#s"/><use href="#s" x="35"/><use href="#s" x="70"/><use href="#s" x="105"/><use href="#s" x="140" fill="none"/></g></svg></div>
  <div class="tname">Curtis Hale</div>
  <div class="tbody">ullamco est sit aliqua dolor do amet sint. Velit officia consequat duis enim velit mollit. Exercitation veniam consequat sunt nostrud...</div>
</div>
<div class="tcard" style="left:786px">
  <div class="avatar" role="img" aria-label="Client portrait"></div>
  <div class="stars"><svg width="168" height="26" viewBox="0 0 168 26"><g fill="#f5a000" stroke="#f5a000" stroke-width="1.5"><use href="#s"/><use href="#s" x="35"/><use href="#s" x="70"/><use href="#s" x="105" fill="none"/><use href="#s" x="140" fill="none"/></g></svg></div>
  <div class="tname">Mara Quinn</div>
  <div class="tbody">Amet minim mollit non deserunt ullamco est sit aliqua dolor do amet sint. Velit officia consequat duis enim velit mollit....</div>
</div>

<!-- footer -->
<div class="abs footer"></div>
<div class="brand" style="left:83px;top:3567px;color:#fff"><i></i>Bramble Acres</div>

<div class="f-head" style="left:417px">FixLine</div>
<div class="f-link" style="left:417px;top:3539px">Endoscope Repair</div>
<div class="f-link" style="left:417px;top:3575px">Used Endoscopes</div>
<div class="f-link" style="left:417px;top:3612px">Accessories</div>
<div class="f-link" style="left:417px;top:3649px">Purchase</div>

<div class="f-head" style="left:642px">About</div>
<div class="f-link" style="left:642px;top:3539px">Support</div>
<div class="f-link" style="left:642px;top:3575px">Contact</div>
<div class="f-link" style="left:642px;top:3612px">Terms</div>
<div class="f-link" style="left:642px;top:3649px">Blog</div>

<div class="f-head" style="left:850px">Subscribe to our Newsletter</div>
<div class="abs" style="left:844px;top:3542px;width:272px;height:58px;border-radius:29px;background:#15264a;display:flex;align-items:center;justify-content:center;color:#6d7a94;font-size:18px">Enter email address</div>
<div class="abs" style="left:844px;top:3609px;width:272px;height:59px;border-radius:30px;background:var(--blue-light);display:flex;align-items:center;justify-content:center;gap:10px;color:#fff;font-size:19px">Submit <svg width="18" height="14" viewBox="0 0 18 14"><path d="M1 7h15M11 2l5 5-5 5" fill="none" stroke="#fff" stroke-width="1.8"/></svg></div>

<div class="abs" style="left:83px;top:3706px;width:1032px;height:1px;background:#1d2d4d"></div>
<div class="abs" style="left:83px;top:3733px;font-size:15px;color:#8a93a6">Copyright © 2022</div>
<div class="social" style="left:980px"></div>
<div class="social" style="left:1018px"></div>
<div class="social" style="left:1056px"></div>
<div class="social" style="left:1094px"></div>

</body>
</html>
```